Meridale Freight online presence/customer portal track shipping

I sleek design showing what we do, broker freight. What we specialize in, chemicals and any freight where domestic or international. We want a home page, a customer portal button on front page that lets clients check on status of their freight (integrate with our transportation management system. Contact page,
COMPANIES THAT HAVE PALLETS TO MOVE.
https://www.tallowmerelogistics.com/
https://www.quivendale.com/
https://www.rkpellow.com/
3 page

```html
<!DOCTYPE html>
<html lang="en">
<head>
<meta charset="utf-8">
<title>Meridale Logistics</title>
<link href="https://fonts.googleapis.com/css2?family=Poppins:wght@500;600;700;800&family=Mulish:wght@400;600;700&display=swap" rel="stylesheet">
<style>
:root{
  --red:#e8333c;
  --blue:#2b60a8;
  --blue-deep:#22508f;
  --ink:#1b1b1b;
  --text:#333;
  --muted:#555;
  --tint:#f5f1f1;
  --white:#fff;
  --teal:#2eae93;
  --footer:#222;
  --line:#d9d4d4;
}
*{margin:0;padding:0;box-sizing:border-box}
html,body{width:1200px;height:4556px;overflow:hidden}
body{font-family:'Mulish',sans-serif;color:var(--text);background:var(--white);position:relative}
section,header,footer{position:absolute;left:0;width:1200px}
.abs{position:absolute}
.heading{font-family:'Poppins',sans-serif;font-weight:600;color:var(--ink);text-align:center;width:100%}
.btn{position:absolute;background:var(--red);color:var(--white);font-family:'Poppins',sans-serif;font-weight:600;font-size:13px;letter-spacing:.5px;border-radius:6px;display:flex;align-items:center;justify-content:center;text-transform:uppercase}

/* hero */
.hero{top:0;height:603px;background:linear-gradient(100deg,#2a2d33 0%,#3b4a3f 40%,#5b6d5a 62%,#9aa3ab 80%,#2e3a30 100%)}
.hero .photo{position:absolute;inset:0}
.brand{position:absolute;left:30px;top:24px;display:flex;align-items:center;gap:12px;font-family:'Poppins',sans-serif;font-weight:600;font-size:27px;color:var(--white)}
.brand .dot{width:32px;height:32px;border-radius:50%;background:var(--white)}
.nav{position:absolute;top:29px;left:468px;display:flex;gap:0;font-family:'Poppins',sans-serif;font-weight:600;font-size:14px;color:var(--white)}
.nav a{color:inherit;text-decoration:none;padding:6px 10px;margin-right:15px}
.nav a.active{background:var(--red)}
.portal{position:absolute;left:1009px;top:25px;width:166px;height:35px;border:2px solid var(--white);border-radius:7px;color:var(--white);font-family:'Poppins',sans-serif;font-weight:600;font-size:13.5px;display:flex;align-items:center;justify-content:center}
.hero h1{position:absolute;left:74px;top:222px;font-family:'Poppins',sans-serif;font-weight:700;font-size:38px;line-height:57px;color:var(--white)}
.dots{position:absolute;top:558px;left:560px;display:flex;gap:11px;align-items:center}
.dots span{width:6px;height:6px;border-radius:50%;background:var(--white)}
.dots span.on{width:11px;height:11px;border:2px solid var(--white);background:var(--red)}

/* intro band */
.intro{top:603px;height:371px;background:linear-gradient(180deg,rgba(43,96,168,.92),rgba(43,96,168,.96)),linear-gradient(90deg,#506a8a,#3a5a86)}
.intro h2{position:absolute;top:96px;font-family:'Poppins',sans-serif;font-weight:600;font-size:30px;color:var(--white);text-align:center;width:100%}
.intro p{position:absolute;top:165px;left:240px;width:720px;text-align:center;font-size:19px;line-height:29px;color:var(--white)}

/* services */
.services{top:974px;height:298px;background:var(--tint)}
.svc{position:absolute;top:0;width:230px;text-align:center}
.svc .icon{margin:33px auto 0;height:89px;width:110px;display:flex;align-items:flex-end;justify-content:center}
.svc h3{margin-top:32px;font-family:'Poppins',sans-serif;font-weight:600;font-size:15px;color:var(--ink)}
.svc p{margin:12px auto 0;width:175px;font-size:12.5px;line-height:17.5px;color:var(--text)}
.divider{position:absolute;top:26px;width:1px;height:216px;background:var(--line)}

/* specialize */
.specialize{top:1272px;height:615px;background:var(--tint);overflow:hidden}
.specialize h2{position:absolute;top:70px;font-size:26px}
.specialize .sub{position:absolute;top:124px;width:100%;text-align:center;font-size:13.5px;color:var(--ink)}
.hub{position:absolute;left:408px;top:332px;width:382px;height:382px;border-radius:50%;background:var(--blue)}
.spec-label{position:absolute;font-family:'Poppins',sans-serif;font-weight:600;font-size:14px;color:var(--ink)}
.ph{position:absolute;border-radius:4px}

/* doing */
.doing{top:1887px;height:910px;background:var(--white)}
.doing h2{position:absolute;top:58px;font-size:26px}
.doing p{position:absolute;top:122px;left:260px;width:680px;text-align:center;font-size:19px;line-height:28px;color:var(--text)}
.map{position:absolute;left:124px;top:253px;width:957px;height:576px;border:3px solid #333;background:linear-gradient(135deg,#cfe6f2,#e9e3c6 45%,#d7e7c8 70%,#bfdcec)}

/* welcome */
.welcome{top:2797px;height:495px;background:var(--tint)}
.welcome .kicker{position:absolute;left:134px;top:70px;font-size:21px;color:var(--ink)}
.welcome h2{position:absolute;left:134px;top:98px;font-family:'Poppins',sans-serif;font-weight:500;font-size:34px;color:var(--ink)}
.welcome .rule{position:absolute;left:134px;top:170px;width:135px;height:1px;background:#999}
.welcome p{position:absolute;left:132px;top:201px;width:345px;font-size:18.5px;line-height:28px;color:var(--text)}
.welcome .photo{position:absolute;left:509px;top:58px;width:560px;height:380px;background:linear-gradient(180deg,#6b5444,#8a6f5a 35%,#c9c5c2 62%,#eef0f2)}

/* blog */
.blog{top:3292px;height:553px;background:var(--blue)}
.blog h2{position:absolute;top:50px;color:var(--white);font-size:26px}
.blog .bar{position:absolute;left:580px;top:100px;width:42px;height:3px;background:var(--white)}
.card{position:absolute;top:163px;width:292px;height:310px;border:2px solid var(--white)}
.card h3{position:absolute;left:27px;top:38px;width:245px;font-family:'Poppins',sans-serif;font-weight:600;font-size:18px;line-height:27px;color:var(--white)}
.card p{position:absolute;left:30px;top:144px;width:220px;font-size:12.5px;line-height:17.5px;color:var(--white)}
.card .btn{left:30px;top:293px;width:96px;height:29px;font-size:11px;border-radius:4px}

/* help */
.help{top:3845px;height:353px;background:var(--teal)}
.help h2{position:absolute;top:62px;width:100%;text-align:center;font-family:'Poppins',sans-serif;font-weight:800;font-size:31px;color:var(--white);letter-spacing:-.5px}
.help p{position:absolute;top:130px;left:280px;width:640px;text-align:center;font-size:18.5px;line-height:29px;color:var(--white)}

/* footer */
.footer{top:4198px;height:358px;background:var(--footer);color:var(--white)}
.f-brand{position:absolute;left:140px;top:87px;display:flex;align-items:center;gap:18px;font-family:'Poppins',sans-serif;font-weight:600;font-size:25px}
.f-brand .dot{width:72px;height:72px;border-radius:50%;background:var(--red)}
.f-col{position:absolute;top:44px;font-size:12px}
.f-col h4{font-family:'Poppins',sans-serif;font-weight:600;font-size:12.5px;letter-spacing:.5px;margin-bottom:20px}
.f-col li{list-style:none;line-height:19.5px}
.f-item{display:flex;align-items:center;gap:15px;margin-bottom:20px;line-height:15px}
.f-item .c{width:22px;height:22px;border-radius:50%;background:var(--white);flex:none;display:flex;align-items:center;justify-content:center}
.f-rule{position:absolute;left:140px;top:246px;width:934px;height:1px;background:#444}
.copy{position:absolute;top:302px;width:100%;text-align:center;font-size:10.5px;color:#ccc}
</style>
</head>
<body>

<header class="hero">
  <div class="photo" role="img" aria-label="Photo of a white semi-trailer truck driving on a forested highway at dusk"></div>
  <div class="brand"><span class="dot"></span>Meridale Logistics</div>
  <nav class="nav">
    <a class="active">HOME</a><a>ABOUT US</a><a>SERVICES</a><a>CAREERS</a><a>CONTACT US</a>
  </nav>
  <div class="portal">CUSTOMER PORTAL</div>
  <h1>Accurately Promising,<br>Reliably Delivering</h1>
  <div class="btn" style="left:74px;top:366px;width:151px;height:44px;font-size:15px">Get Started</div>
  <div class="dots"><span></span><span></span><span class="on"></span><span></span><span></span></div>
</header>

<section class="intro" role="img" aria-label="Blue-tinted band over a photo of trucks on a highway">
  <h2>Global Integrated Logistics</h2>
  <p>Meridale Logistics specializes in moving regulated and non-regulated chemical freight of all kinds Operating in 49 states and Canada Meridale Logistics' focus is in brokering van or flatbed, tanker endorsed, liquid bulk, drayage, intermodal, and international chemical shipments of all combinations.</p>
</section>

<section class="services">
  <div class="svc" style="left:134px">
    <div class="icon"><svg width="110" height="54" viewBox="0 0 110 54" fill="none" stroke="#2b60a8" stroke-width="2.5"><rect x="2" y="2" width="76" height="36"/><path d="M78 14h18l10 12v12H78z"/><circle cx="20" cy="46" r="6"/><circle cx="36" cy="46" r="6"/><circle cx="92" cy="46" r="6"/></svg></div>
    <h3>Expedited freight</h3>
    <p>Meeting deadlines is everything to the recipient of the shipment. With teams and dedicated carriers Meridale logistics happen.</p>
  </div>
  <div class="divider" style="left:364px"></div>
  <div class="svc" style="left:364px">
    <div class="icon"><svg width="60" height="66" viewBox="0 0 60 66" fill="none" stroke="#2b60a8" stroke-width="2.5"><path d="M4 2h36l14 14v48H4z"/><path d="M40 2v14h14"/><path d="M12 26h32M12 36h32M12 46h22"/></svg></div>
    <h3>Contract Logistics</h3>
    <p>With a network of carriers and contracted lanes of freight. Meridale logistics is capable of staying below market rates.</p>
  </div>
  <div class="divider" style="left:599px"></div>
  <div class="svc" style="left:595px">
    <div class="icon"><svg width="70" height="72" viewBox="0 0 70 72" fill="none" stroke="#2b60a8" stroke-width="2.5"><path d="M40 4c-8 10 10 16 0 28s-26 10-22 24 20 12 20 12"/><path d="M52 4c-6 12 10 18 0 30s-24 8-20 22 18 12 18 12"/><circle cx="14" cy="18" r="7"/></svg></div>
    <h3>Road Freight</h3>
    <p>There are many variations of passages of Lorem Ipsum available, but the majority have suffered alter.</p>
  </div>
  <div class="divider" style="left:834px"></div>
  <div class="svc" style="left:834px">
    <div class="icon"><svg width="96" height="86" viewBox="0 0 96 86" fill="none" stroke="#2b60a8" stroke-width="2.5"><rect x="32" y="10" width="28" height="24"/><path d="M46 2v8"/><rect x="30" y="38" width="60" height="30"/><path d="M30 48H14L4 60v8h26"/><circle cx="18" cy="74" r="7"/><circle cx="72" cy="74" r="7"/></svg></div>
    <h3>Intermodal</h3>
    <p>There are many variations of passages of Lorem Ipsum available, but the majority have suffered alter.</p>
  </div>
</section>

<section class="specialize">
  <h2 class="heading">We Specialize In</h2>
  <div class="sub">There are many variations of passages of Lorem Ipsum available lorem ipsum</div>
  <svg class="abs" style="left:0;top:0" width="1200" height="615" stroke="#cfc9c9" stroke-width="1.5">
    <line x1="292" y1="209" x2="486" y2="347"/>
    <line x1="147" y1="398" x2="375" y2="477"/>
    <line x1="919" y1="209" x2="716" y2="345"/>
    <line x1="1066" y1="398" x2="830" y2="477"/>
  </svg>
  <div class="hub"></div>

  <div class="ph" style="left:525px;top:233px;width:127px;height:32px;background:linear-gradient(90deg,#c8202a 25%,#f2f2f2 25%)" role="img" aria-label="Dry van truck illustration"></div>
  <div class="spec-label" style="left:567px;top:285px">Dry Van</div>

  <div class="ph" style="left:238px;top:322px;width:108px;height:49px;background:linear-gradient(90deg,#d22a2f 50%,#333 50%)" role="img" aria-label="Flammable and corrosive hazard placards"></div>
  <div class="spec-label" style="left:355px;top:358px">Hazmat</div>

  <div class="spec-label" style="left:777px;top:363px">Hot Shots/Box Trucks</div>
  <div class="ph" style="left:945px;top:329px;width:82px;height:51px;background:linear-gradient(90deg,#1f1f1f 35%,#f2f2f2 35%)" role="img" aria-label="Box truck illustration"></div>

  <div class="ph" style="left:148px;top:500px;width:101px;height:30px;background:linear-gradient(90deg,#d22a2f 55%,#2b60a8 55%)" role="img" aria-label="LTL partial load truck illustration"></div>
  <div class="spec-label" style="left:281px;top:508px">LTL/Partials</div>

  <div class="spec-label" style="left:839px;top:508px">Drayage/Intermodal</div>
  <div class="ph" style="left:1000px;top:497px;width:110px;height:37px;background:linear-gradient(90deg,#1f1f1f 25%,#555 25%)" role="img" aria-label="Container drayage truck illustration"></div>
</section>

<section class="doing">
  <h2 class="heading">What We Are Doing</h2>
  <p>Meridale Logistics is developing a nationwide network of hub shipping locations for connecting our customers, suppliers, and their consumers with carriers moving throughout the interconnected lanes.</p>
  <div class="map" role="img" aria-label="Map of the United States with shipping lanes radiating from hub cities"></div>
</section>

<section class="welcome">
  <div class="kicker">Welcome to</div>
  <h2>Meridale Logistics</h2>
  <div class="rule"></div>
  <p>Success is won by those who believe in winning, and then prepare for that moment. Many want to win, but how many prepare? That is the big difference. - Hal Brenner</p>
  <div class="btn" style="left:134px;top:382px;width:108px;height:35px">Read More</div>
  <div class="photo" role="img" aria-label="Photo of a hockey team celebrating on the ice in front of a cheering crowd"></div>
</section>

<section class="blog">
  <h2 class="heading">Latest Blog</h2>
  <div class="bar"></div>
  <article class="card" style="left:140px">
    <h3>Lorem Ipsum is simply dummy text of the printing and typesetting industry</h3>
    <p>Sed ut perspiciatis unde omnis iste natus error sit voluptatem accusantium doloremque laudantium, totam rem aperiam, eaque ipsa quae ab illo inventore veritatis et quasi architecto beatae vitae dicta s</p>
    <div class="btn">Read More</div>
  </article>
  <article class="card" style="left:461px">
    <h3>Lorem Ipsum is simply dummy text of the printing and typesetting industry</h3>
    <p>Sed ut perspiciatis unde omnis iste natus error sit voluptatem accusantium doloremque laudantium, totam rem aperiam, eaque ipsa quae ab illo inventore veritatis et quasi architecto beatae vitae dicta s</p>
    <div class="btn">Read More</div>
  </article>
  <article class="card" style="left:782px">
    <h3>Lorem Ipsum is simply dummy text of the printing and typesetting industry</h3>
    <p>Sed ut perspiciatis unde omnis iste natus error sit voluptatem accusantium doloremque laudantium, totam rem aperiam, eaque ipsa quae ab illo inventore veritatis et quasi architecto beatae vitae dicta s</p>
    <div class="btn">Read More</div>
  </article>
</section>

<section class="help">
  <h2>HOW CAN WE HELP YOU?</h2>
  <p>At vero eos et accusamus et iusto odio dignissimos ducimus qui blanditiis praesentium voluptatum deleniti atque corrupti quos dolores et quas molestias excepturi sint occaecati cupiditate non provident,</p>
  <div class="btn" style="left:520px;top:258px;width:137px;height:39px;font-size:12px">Contact Us</div>
</section>

<footer class="footer">
  <div class="f-brand"><span class="dot"></span>Meridale Freight</div>
  <div class="f-col" style="left:486px">
    <h4>MENU</h4>
    <ul><li>HOME</li><li>ABOUT US</li><li>SERVICES</li><li>CAREERS</li><li>CONTACT US</li></ul>
  </div>
  <div class="f-col" style="left:677px">
    <h4>CONTACT US</h4>
    <div class="f-item"><span class="c"><svg width="10" height="12" viewBox="0 0 10 12"><path d="M5 0a4 4 0 0 0-4 4c0 3 4 8 4 8s4-5 4-8a4 4 0 0 0-4-4z" fill="#222"/></svg></span><span>2650 Alder Crest Road<br>Fenwick, CA 90000</span></div>
    <div class="f-item"><span class="c"><svg width="11" height="11" viewBox="0 0 11 11"><path d="M2 0l2 3-1 1.5a6 6 0 0 0 3.5 3.5L8 7l3 2-1 2C5 11 0 6 0 1z" fill="#222"/></svg></span><span>Call Us<br>800.555.0142</span></div>
    <div class="f-item"><span class="c"><svg width="11" height="8" viewBox="0 0 11 8"><rect width="11" height="8" fill="#222"/><path d="M0 0l5.5 4L11 0" stroke="#fff" fill="none"/></svg></span><span>E mail Us<br>info@meridalefreight.com</span></div>
  </div>
  <div class="f-col" style="left:968px">
    <h4>FOLLOW US</h4>
    <div class="f-item"><span class="c"></span><span>Like us on<br>FRIENDWALL</span></div>
    <div class="f-item"><span class="c"></span><span>Follow us on<br>CHIRPLINE</span></div>
    <div class="f-item"><span class="c"></span><span>Follow us on<br>WORKROLL</span></div>
  </div>
  <div class="f-rule"></div>
  <div class="copy">Copyright © 2021 All Rights Reserved</div>
</footer>

</body>
</html>
```